Need business card with a logo for a hearing aid sales and audiology business. We have two Hearing Instrument Specialists and one Audiologist on staff. Over 25 years in business. Locally owned and operated. Financing available. Most insurances accepted.

Summit Audio Wellness LLC
48730 W Larchmont, Suite 7
Spokane, WA 99281
509-617-2084
www.summitaudiowell.example

Manager
Tobias Kerrell HIS COHC
License #71829046

Target Market(s)

50yr old + people with a hearing loss.

Industry/Entity Type

Business

Contact Information for Business Card

48730 W Larchmont, Suite 7
Spokane, WA 99281
509-617-2084
www.summitaudiowell.example

Manager
Tobias Kerrell HIS COHC
NLVE #71829046

Font styles to use
Serif
Sans Serif

Requirements
Must have
• Business name, Tobias's name and title(s) and contact information, License #, web address

```html
<!DOCTYPE html>
<html lang="en">
<head>
<meta charset="utf-8">
<title>Summit Audio Wellness – Business Card</title>
<link href="https://fonts.googleapis.com/css2?family=Open+Sans:wght@400;600;700&display=swap" rel="stylesheet">
<style>
  :root {
    --navy: #1a4a8f;
    --royal: #0a6ab8;
    --rule: #b9bcc2;
    --ink: #2b2b2b;
    --paper: #ffffff;
    --backdrop: #e9eaec;
  }
  * { box-sizing: border-box; margin: 0; padding: 0; }
  html, body { width: 1200px; height: 1000px; overflow: hidden; }
  body {
    background: var(--backdrop);
    font-family: "Open Sans", Arial, sans-serif;
    color: var(--ink);
    position: relative;
  }
  .card {
    position: absolute;
    left: 265px;
    width: 666px;
    height: 397px;
    box-shadow: 0 4px 14px rgba(0,0,0,0.18);
  }
  .card-front { top: 73px; background: var(--paper); }
  .card-back { top: 532px; background: var(--navy); }

  .brand {
    position: absolute;
    display: flex;
    align-items: center;
    font-weight: 400;
    line-height: 1.05;
  }
  .brand-dot { border-radius: 50%; flex: none; }
  .brand-front { left: 32px; top: 48px; color: var(--navy); font-size: 34px; gap: 14px; }
  .brand-front .brand-dot { width: 46px; height: 46px; background: var(--navy); }
  .brand-back { left: 0; right: 0; top: 150px; justify-content: center; color: var(--paper); font-size: 44px; gap: 18px; }
  .brand-back .brand-dot { width: 58px; height: 58px; background: var(--paper); }

  .person {
    position: absolute;
    right: 33px;
    top: 207px;
    text-align: right;
  }
  .person-name {
    color: var(--navy);
    font-weight: 700;
    font-size: 20px;
    text-transform: uppercase;
    letter-spacing: 0.2px;
  }
  .person-name .credentials { font-weight: 400; font-size: 16px; margin-left: 4px; }
  .person-role { font-size: 15.5px; line-height: 25px; margin-top: 12px; }

  .divider {
    position: absolute;
    left: 180px;
    right: 33px;
    top: 240px;
    height: 1px;
    background: var(--rule);
  }

  .contact {
    position: absolute;
    left: 33px;
    top: 230px;
    font-size: 15.5px;
    line-height: 24px;
  }
  .contact-line { display: flex; align-items: center; gap: 7px; }
  .contact-line svg { width: 15px; height: 15px; fill: var(--navy); }
  .address { margin-top: 7px; line-height: 21px; }
  .address .company { font-weight: 700; }
  .address .company span { font-weight: 400; }

  .card-band { position: absolute; left: 0; bottom: 0; width: 666px; height: 24px; display: block; }
</style>
</head>
<body>
  <section class="card card-front">
    <div class="brand brand-front">
      <span class="brand-dot"></span>
      <span class="brand-name">Summit Audio<br>Wellness</span>
    </div>

    <div class="person">
      <div class="person-name">Tobias Kerrell<span class="credentials">HIS COHC</span></div>
      <div class="person-role">Manager<br>License #71829046</div>
    </div>
    <div class="divider"></div>

    <div class="contact">
      <div class="contact-line">
        <svg viewBox="0 0 16 16" aria-hidden="true"><path d="M1 6c0-2 3-4 7-4s7 2 7 4v1h-3.5V5.5h-7V7H1z"/><path d="M3.5 8h9l1.5 6H2z"/></svg>
        509-617-2084
      </div>
      <div class="contact-line">
        <svg viewBox="0 0 16 16" aria-hidden="true"><circle cx="8" cy="8" r="7"/><path d="M1 8h14M8 1c3 3 3 11 0 14M8 1c-3 3-3 11 0 14" stroke="#fff" stroke-width="1.1" fill="none"/></svg>
        www.summitaudiowell.example
      </div>
      <div class="address">
        <div class="company">Summit Audio Wellness <span>LLC</span></div>
        <div>48730 W Larchmont, Suite 7</div>
        <div>Spokane, WA 99281</div>
      </div>
    </div>

    <svg class="card-band" viewBox="0 0 666 24" preserveAspectRatio="none" aria-hidden="true">
      <polygon points="0,2 340,2 318,24 0,24" fill="var(--navy)"/>
      <polygon points="352,0 666,0 666,24 330,24" fill="var(--royal)"/>
    </svg>
  </section>

  <section class="card card-back">
    <div class="brand brand-back">
      <span class="brand-dot"></span>
      <span class="brand-name">Summit Audio<br>Wellness</span>
    </div>
  </section>
</body>
</html>
```